Annual Report Velomar 2025

Take a PowerPoint presentation and turn it into a info graphic type annual report, posters and flyers.

Annual report ideally no more than 8 pages.

Please use the colours and fonts in the attached brand guidelines.

We are looking for an infographic visually appealing piece.

```html
<!DOCTYPE html>
<html lang="en">
<head>
<meta charset="utf-8">
<title>Velomar 2025 Annual Report – Spreads</title>
<link rel="stylesheet" href="https://fonts.googleapis.com/css2?family=Playfair+Display:ital,wght@0,700;1,700&family=Nunito+Sans:ital,wght@0,400;0,600;0,700;0,800;1,600&display=swap">
<style>
:root{
  --navy:#0b2f5b;
  --navy-deep:#082649;
  --green:#7ab03a;
  --green-soft:#d5eaa6;
  --blue-soft:#dcebfa;
  --ink:#1d2a3a;
  --white:#ffffff;
  --backdrop:#b2b2b4;
}
*{margin:0;padding:0;box-sizing:border-box}
html,body{width:1200px;height:927px;overflow:hidden;background:var(--backdrop)}
body{position:relative;font-family:"Nunito Sans",Arial,sans-serif;color:var(--ink)}
.page{position:absolute;width:271px;height:384px;background:var(--white);overflow:hidden;box-shadow:0 2px 6px rgba(0,0,0,.25)}
.abs{position:absolute}
.title{position:absolute;left:27px;top:20px;font-family:"Playfair Display",Georgia,serif;font-weight:700;font-size:20px;color:var(--navy);letter-spacing:.1px;white-space:nowrap}
.rule{position:absolute;left:27px;top:55px;width:34px;height:2px;background:var(--green)}
.lead{font-weight:700;color:var(--navy);font-size:7.4px;line-height:1.45}
.body{font-size:7.2px;line-height:1.45;color:var(--ink)}
.footer{position:absolute;left:0;bottom:0;width:271px;height:41px;background:var(--navy);display:flex;align-items:center;justify-content:space-between;padding:0 17px 0 21px;color:var(--white);font-size:7.6px}
.brand{display:flex;align-items:center;gap:3px;font-weight:800;color:var(--white);font-size:11px}
.brand .dot{width:8px;height:8px;border-radius:50%;border:1.3px solid var(--white)}
.green{color:var(--green)}
.stat-card{position:absolute;top:141px;width:74px;height:134px;border-radius:4px;text-align:center;padding-top:22px;font-size:7.4px;line-height:1.4}
.stat-card svg{width:40px;height:40px;margin-bottom:10px}
.stat-card .figure{font-weight:700;color:var(--green);display:block}
.pillar{position:absolute;top:12px;width:88px;text-align:center;color:var(--white)}
.pillar h4{font-size:9px;font-weight:800;line-height:1.05;margin-top:4px}
.pillar p{font-size:3.9px;margin-top:5px;line-height:1.35;opacity:.9}
.pillar svg{width:38px;height:34px}
.commit{position:absolute;width:74px;height:71px;background:var(--green-soft);border-radius:3px;text-align:center;color:var(--navy);font-size:7.2px;font-weight:700;line-height:1.3;padding-top:6px}
.commit svg{width:44px;height:36px;display:block;margin:0 auto 2px}
.service{position:absolute;left:24px;width:240px;height:66px}
.service .disc{position:absolute;left:0;top:0;width:66px;height:66px;border-radius:50%;display:flex;align-items:center;justify-content:center}
.service svg{width:38px;height:38px}
.service h3{position:absolute;left:85px;top:13px;font-size:9px;font-weight:700;color:var(--navy)}
.service p{position:absolute;left:85px;top:29px;width:140px;font-size:7.2px;font-weight:600;line-height:1.45;color:var(--ink)}
.divider{position:absolute;left:24px;width:228px;height:1px;background:var(--navy)}
.hl{position:absolute;width:120px;text-align:center;color:var(--white);font-size:7.4px;line-height:1.35}
.hl .disc{width:66px;height:66px;border-radius:50%;background:var(--green);margin:0 auto 9px;display:flex;align-items:center;justify-content:center}
.hl .disc svg{width:40px;height:40px}
.hl .big{display:block;color:var(--green);font-weight:700;font-size:8.8px}
.prog{position:absolute;width:122px;border-radius:4px;padding:8px 6px 6px 35px;font-size:7.3px;line-height:1.3}
.prog svg{position:absolute;left:5px;top:8px;width:26px;height:26px}
.prog h5{font-size:7.6px;font-weight:700;margin-bottom:6px;line-height:1.3}
.prog ul{margin-left:10px}
.contact{position:absolute;left:20px;display:flex;align-items:center;gap:10px;color:var(--white);font-size:7.6px;font-weight:700}
.contact svg{width:14px;height:14px}
</style>
</head>
<body>

<!-- Cover -->
<section class="page" style="left:12px;top:58px;background:var(--navy)">
  <div class="abs" role="img" aria-label="Photograph of four hikers celebrating on a mountain summit at sunrise above a river valley" style="left:0;top:0;width:271px;height:344px;background:linear-gradient(180deg,#0d3470 0%,#2e5d9a 30%,#e7b15a 52%,#8a5a2c 66%,#3a3524 82%,#1a1c18 100%)"></div>
  <div class="abs brand" style="left:29px;top:20px;font-size:15px"><span class="dot" style="width:11px;height:11px"></span>Velomar</div>
  <div class="abs" style="left:27px;top:47px;font-family:'Playfair Display',Georgia,serif;font-weight:700;color:var(--white);font-size:22px;line-height:1.0">2025<br>Annual Report</div>
  <div class="abs" style="left:27px;top:94px;font-size:7.4px;font-style:italic;font-weight:600;color:var(--green)">Resilience Through Partnership</div>
  <div class="abs" style="left:27px;top:323px;font-size:12.5px;font-weight:800;color:var(--white)">Values Driving <span class="green">Value</span></div>
  <div class="footer" style="justify-content:flex-start;gap:8px;font-size:6px;line-height:1.05">
    <svg width="18" height="20" viewBox="0 0 18 20" fill="none" stroke="#7ab03a" stroke-width="1.3"><path d="M9 1a5.5 5.5 0 0 0-5.5 5.5C3.5 11 9 16 9 16s5.5-5 5.5-9.5A5.5 5.5 0 0 0 9 1z"/><circle cx="9" cy="6.5" r="2"/><ellipse cx="9" cy="17.5" rx="6" ry="1.5"/></svg>
    <span style="width:96px">18 Harrow Lane East,<br>Brantford, ON</span>
    <svg width="18" height="20" viewBox="0 0 18 20" fill="none" stroke="#7ab03a" stroke-width="1.2"><rect x="1.5" y="2" width="12" height="16" rx="1"/><path d="M4 6h7M4 9h7M4 12h5M14 5l3 3-6 7-3 1 1-3z"/></svg>
    <span>Charitable Registration<br>#: 40912 5538 RR0001</span>
  </div>
</section>

<!-- Executive Summary -->
<section class="page" style="left:313px;top:58px">
  <h2 class="title">Executive Summary</h2>
  <div class="rule"></div>
  <p class="abs lead" style="left:27px;top:66px;width:190px">2025 marked a significant year of growth and stewardship for Velomar.</p>
  <p class="abs body" style="left:27px;top:93px;width:175px">We surpassed $100 million in assets under management and facilitated over $6 million in grants across Canada.</p>
  <div class="stat-card" style="left:20px;background:var(--navy);color:var(--white)">
    <svg viewBox="0 0 40 40" fill="none" stroke="#fff" stroke-width="1.3"><rect x="2" y="6" width="18" height="4" rx="1"/><rect x="2" y="12" width="14" height="4" rx="1"/><rect x="2" y="18" width="14" height="4" rx="1"/><rect x="2" y="24" width="14" height="4" rx="1"/><rect x="2" y="30" width="16" height="4" rx="1"/><circle cx="26" cy="20" r="11"/><circle cx="26" cy="20" r="8.5"/><path d="M28.5 16.5c-1-1-4.5-1.5-4.8.7-.3 2.6 5 1.2 4.8 4-.2 2.3-3.8 1.9-5 .7M26 14v12"/></svg>
    <span class="figure">$100M+</span>Assets Under<br>Management
  </div>
  <div class="stat-card" style="left:99px;background:var(--blue-soft);color:var(--navy)">
    <svg viewBox="0 0 40 40" fill="none" stroke="#0b2f5b" stroke-width="1.3"><path d="M20 16c-2-4-8-3-7 2 .6 3 7 7 7 7s6.4-4 7-7c1-5-5-6-7-2z"/><path d="M4 8l3 14 8 10v5M36 8l-3 14-8 10v5M9 16l4 8M31 16l-4 8"/></svg>
    <span class="figure">$6M+</span>Grants<br>Facilitated
  </div>
  <div class="stat-card" style="left:178px;background:var(--green-soft);color:var(--navy)">
    <svg viewBox="0 0 40 40" fill="none" stroke="#0b2f5b" stroke-width="1.3"><rect x="6" y="8" width="28" height="20" rx="1.5"/><path d="M2 31h36l-2 3H4z"/><circle cx="20" cy="17" r="5"/><circle cx="20" cy="17" r="7.5" stroke-dasharray="2 2"/></svg>
    <span class="figure">New Services</span>Investment &amp;<br>Bookkeeping<br>Support
  </div>
  <p class="abs body" style="left:27px;top:286px;width:220px">Together with our partners, we strengthened communities, supported meaningful initiatives, and built capacity for lasting impact.</p>
  <footer class="footer"><span class="brand"><span class="dot"></span>Velomar</span><span>2025 Annual Report</span></footer>
</section>

<!-- Who We Are -->
<section class="page" style="left:614px;top:58px">
  <h2 class="title" style="font-size:18.5px">Who We Are</h2>
  <div class="rule"></div>
  <p class="abs lead" style="left:27px;top:66px;width:98px">Velomar is a Canadian public foundation committed to the faithful stewardship of generosity.</p>
  <div class="abs body" style="left:27px;top:113px;width:112px;font-size:6.6px">
    <p>We come alongside donors, families, and organizations to transform charitable intent into thoughtful, lasting impact through:</p>
    <ul style="margin:9px 0 9px 12px"><li>Donor-Advised Funds</li><li>Disciplined Investment Management</li><li>Purposeful Granting</li></ul>
    <p>Rooted in trust, integrity, and care, we take a long-term approach—serving both present needs and future generations.</p>
  </div>
  <div class="abs" role="img" aria-label="Photograph of a young seedling growing from dark soil in warm sunlight" style="left:142px;top:0;width:129px;height:260px;background:radial-gradient(circle at 30% 20%,#d8c77a 0%,#6d8c3a 30%,#2f4a1e 60%,#2a1e12 100%)"></div>
  <div class="abs" style="left:0;top:260px;width:271px;height:124px;background:var(--navy)">
    <div class="pillar" style="left:3px"><svg viewBox="0 0 38 34" fill="none" stroke="#7ab03a" stroke-width="1.3"><path d="M2 12l8-6 6 3 6-3 6 3 8-3M4 14l12 12c2 2 4 0 2-2M14 22c2 2 4 0 2-2M17 19c2 2 4 0 2-2M36 14L24 26M9 7l9 10"/></svg><h4>Trusted<br>Partnership</h4><p>We walk alongside our partners<br>with care and accountability</p></div>
    <div class="abs" style="left:95px;top:14px;width:1px;height:80px;background:#7f93ad"></div>
    <div class="pillar" style="left:92px"><svg viewBox="0 0 38 34" fill="none" stroke="#7ab03a" stroke-width="1.3"><path d="M12 30C8 20 14 6 32 3c1 14-6 24-18 24zM12 30l14-20M18 22h6M20 17h6M16 16l2 5"/></svg><h4>Thoughtful<br>Stewardship</h4><p>We manage resources with<br>wisdom and integrity</p></div>
    <div class="abs" style="left:187px;top:14px;width:1px;height:80px;background:#7f93ad"></div>
    <div class="pillar" style="left:180px"><svg viewBox="0 0 38 34" fill="none" stroke="#7ab03a" stroke-width="1.3"><path d="M8 28v-6h4v6M14 28v-10h4v10M20 28v-14h4v14M6 18l8-8 5 3 9-10M24 3h4v4"/><circle cx="30" cy="22" r="2"/><circle cx="34" cy="24" r="2"/><path d="M27 30v-3h6v3"/></svg><h4>Lasting<br>Impact</h4><p>We focus on outcomes that<br>create enduring change</p></div>
  </div>
  <footer class="footer" style="background:transparent"><span class="brand"><span class="dot"></span>Velomar</span><span>2025 Annual Report</span></footer>
</section>

<!-- Guiding Principles -->
<section class="page" style="left:916px;top:58px">
  <h2 class="title">Guiding Principles</h2>
  <div class="rule"></div>
  <p class="abs lead" style="left:27px;top:66px;width:222px;color:var(--ink)">Velomar integrates responsible investing by considering environmental, social, and governance (ESG) factors.</p>
  <p class="abs body" style="left:27px;top:91px;width:222px">Our approach ensures that every investment aligns with our mission and values while creating meaningful impact.</p>
  <p class="abs" style="left:27px;top:167px;font-size:7.4px;font-weight:800;color:var(--navy);letter-spacing:.2px">OUR COMMITMENTS</p>
  <div class="commit" style="left:20px;top:182px"><svg viewBox="0 0 44 36" fill="none" stroke="#0b2f5b" stroke-width="1.3"><circle cx="10" cy="6" r="4"/><circle cx="22" cy="6" r="4"/><circle cx="34" cy="6" r="4"/><path d="M4 30V16c0-3 3-4 6-4s6 1 6 4v14M16 30V16c0-3 3-4 6-4s6 1 6 4v14M28 30V16c0-3 3-4 6-4s6 1 6 4v14"/></svg>Respect<br>Human Rights</div>
  <div class="commit" style="left:99px;top:182px"><svg viewBox="0 0 44 36" fill="none" stroke="#0b2f5b" stroke-width="1.3"><path d="M6 26c0-12 8-20 18-20s14 8 14 16M2 26c10 4 30 4 40-4M18 7l3 15M28 8l-2 14"/></svg>Respect<br>Workers’ Rights</div>
  <div class="commit" style="left:178px;top:182px"><svg viewBox="0 0 44 36" fill="none" stroke="#0b2f5b" stroke-width="1.3"><path d="M22 3v28M14 32h16M8 8h28M8 8L3 20h10zM36 8l-5 12h10zM3 20c0 3 10 3 10 0M31 20c0 3 10 3 10 0"/></svg>Economic &amp;<br>Social Justice</div>
  <div class="commit" style="left:20px;top:260px"><svg viewBox="0 0 44 36" fill="none" stroke="#0b2f5b" stroke-width="1.3"><path d="M22 34C18 22 22 8 32 2c2 12-2 24-10 32zM22 34C14 28 6 26 4 20c8-1 14 4 18 14z"/></svg>Environmental<br>Sustainability</div>
  <div class="commit" style="left:99px;top:260px"><svg viewBox="0 0 44 36" fill="none" stroke="#0b2f5b" stroke-width="1.3"><path d="M6 4c4 8 8 12 14 14l6-6 4 1-2 3c2 6-4 14-14 14l4-4c-6 0-10-4-12-8 4 0 6 0 8-1C10 14 6 10 6 4zM30 13l6-8M33 9l4-1"/></svg>Global<br>Peace</div>
  <div class="commit" style="left:178px;top:260px"><svg viewBox="0 0 44 36" fill="none" stroke="#0b2f5b" stroke-width="1.3"><circle cx="22" cy="18" r="15"/><ellipse cx="22" cy="18" rx="6" ry="15"/><path d="M7 18h30M10 10h24M10 26h24M22 3v30"/></svg>ESG Decision<br>Making</div>
  <footer class="footer"><span class="brand"><span class="dot"></span>Velomar</span><span>2025 Annual Report</span></footer>
</section>

<!-- Our Services -->
<section class="page" style="left:18px;top:484px">
  <h2 class="title">Our Services</h2>
  <p class="abs" style="left:27px;top:48px;font-size:11.5px;font-style:italic;font-weight:600;color:var(--green)">3 Ways to Increase Revenue</p>
  <div class="service" style="top:78px"><div class="disc" style="background:var(--navy)"><svg viewBox="0 0 38 38" fill="#fff"><rect x="3" y="24" width="5" height="10"/><rect x="10" y="18" width="5" height="16"/><rect x="17" y="12" width="5" height="22"/><path d="M3 20L20 6l3 3 6-6v6h-2l0-2-4 4-3-3L4 22z"/><circle cx="28" cy="27" r="8" fill="none" stroke="#fff" stroke-width="2"/><path d="M30 24c-1-1-4-1-4 1s4 1 4 3-3 2-4 1M28 22v10" stroke="#fff" stroke-width="1.4" fill="none"/></svg></div><h3>Investment Support</h3><p>Disciplined, values-aligned investment management designed for long-term growth and stability.</p></div>
  <div class="divider" style="top:151px"></div>
  <div class="service" style="top:158px"><div class="disc" style="background:var(--green)"><svg viewBox="0 0 38 38" fill="#fff"><rect x="2" y="4" width="4" height="9"/><path d="M7 5h10l4 3-4 2h-6v2h10l3 2H7z"/><rect x="16" y="16" width="10" height="8"/><rect x="32" y="24" width="4" height="9"/><path d="M31 25H20l-4 3 4 2h5v2H12l-2-2c0 2 0 4 2 4h19z"/></svg></div><h3>Revenue Development</h3><p>Connecting generosity with impactful initiatives that strengthen communities.</p></div>
  <div class="divider" style="top:231px"></div>
  <div class="service" style="top:238px"><div class="disc" style="background:var(--navy)"><svg viewBox="0 0 38 38"><path d="M19 20s-9-5-9-10c0-5 7-6 9-1 2-5 9-4 9 1 0 5-9 10-9 10z" fill="#7ab03a"/><path d="M2 26c5-1 9-1 13 1h7c2 0 2 3 0 3h-6h8l9-4c2-1 4 1 2 3l-11 6H11l-9-3z" fill="#fff"/></svg></div><h3>Charitable Grant Programs</h3><p>Connecting generosity with impactful initiatives that strengthen communities.</p></div>
  <p class="abs body" style="left:27px;top:311px;width:210px">We provide practical tools and expert guidance to help organizations grow sustainably.</p>
  <footer class="footer"><span class="brand"><span class="dot"></span>Velomar</span><span>2025 Annual Report</span></footer>
</section>

<!-- 2025 Highlights -->
<section class="page" style="left:313px;top:484px">
  <h2 class="title">2025 Highlights</h2>
  <div class="rule"></div>
  <div class="abs" style="left:0;top:60px;width:271px;height:279px;background:var(--navy)">
    <div class="abs" style="left:135px;top:34px;width:1px;height:104px;background:#c9d3df"></div>
    <div class="abs" style="left:22px;top:143px;width:228px;height:1px;background:#c9d3df"></div>
    <div class="abs" style="left:136px;top:152px;width:1px;height:104px;background:#c9d3df"></div>
    <div class="hl" style="left:2px;top:24px"><div class="disc"><svg viewBox="0 0 40 40" fill="none" stroke="#0b2f5b" stroke-width="1.6"><ellipse cx="15" cy="8" rx="10" ry="4"/><path d="M5 8v5c0 2 4 4 10 4s10-2 10-4V8M3 17v5c0 2 4 4 10 4M3 26v5c0 2 4 4 10 4"/><circle cx="28" cy="27" r="9"/><path d="M30 24c-1-1-4-1-4 1s4 1 4 3-3 2-4 1M28 22v10"/></svg></div><span class="big">$100 MILLION</span>Assets Under<br>Management</div>
    <div class="hl" style="left:148px;top:24px"><div class="disc"><svg viewBox="0 0 40 40" fill="none" stroke="#0b2f5b" stroke-width="1.6"><path d="M22 20s-8-5-8-10c0-5 6-6 8-1 2-5 8-4 8 1 0 5-8 10-8 10z"/><path d="M2 26c5-1 9-1 13 1h7c2 0 2 3 0 3h-6 8l9-5c2-1 4 1 2 3l-11 7H11l-9-3"/></svg></div><span class="big">$6 MILLION</span>Granted to Charities<br>Across Canada</div>
    <div class="hl" style="left:2px;top:152px;text-align:left;padding-left:32px;width:130px"><div class="disc" style="margin-left:0"><svg viewBox="0 0 40 40" fill="none" stroke="#0b2f5b" stroke-width="1.6"><path d="M12 4h16l5 5v16M28 4v5h5"/><rect x="4" y="16" width="14" height="20" rx="2"/><path d="M7 20h8M7 25h2M11 25h2M15 25h0M7 29h2M11 29h2M7 33h2M11 33h2"/><circle cx="28" cy="28" r="8"/><path d="M30 25c-1-1-4-1-4 1s4 1 4 3-3 2-4 1M28 23v10"/></svg></div><span style="font-weight:700;font-size:8.8px;line-height:1.4;display:block"><span class="green">New</span> Money Market Portfolio</span>Supporting donor<br>needs</div>
    <div class="hl" style="left:148px;top:152px;text-align:left;padding-left:0;width:120px"><div class="disc" style="margin-left:0"><svg viewBox="0 0 40 40" fill="none" stroke="#0b2f5b" stroke-width="1.6"><path d="M10 3h16l6 6v28H10z M26 3v6h6M8 7v32h22"/><path d="M14 28v-4M18 28v-7M22 28v-10M26 28v-5M13 17l5-4 4 2 5-5M13 32h16"/></svg></div><span style="font-weight:700;font-size:8.8px;line-height:1.4;display:block">Expanded Support Services</span>Bookkeeping &amp;<br>administrative support</div>
  </div>
  <footer class="footer"><span class="brand"><span class="dot"></span>Velomar</span><span>2025 Annual Report</span></footer>
</section>

<!-- Impact & Programs -->
<section class="page" style="left:614px;top:484px">
  <h2 class="title">Our Impact &amp; Programs</h2>
  <div class="rule"></div>
  <div class="prog" style="left:10px;top:90px;height:101px;background:var(--navy);color:var(--white)"><svg viewBox="0 0 26 26" fill="none" stroke="#7ab03a" stroke-width="1.1"><circle cx="14" cy="10" r="7"/><path d="M14 3v14M8 7h12M1 19c4-1 6-1 9 0h5c1 0 1 2 0 2h-4 6l6-3c1 0 2 1 1 2l-8 5H8l-7-2"/></svg><h5 style="margin-bottom:4px">Faith-Based Responsible Investing</h5>We integrate ESG principles into all investment decisions, ensuring alignment with ethical and mission-driven values.</div>
  <div class="prog" style="left:140px;top:90px;height:101px;background:var(--green-soft);color:var(--navy)"><svg viewBox="0 0 26 26" fill="none" stroke="#0b2f5b" stroke-width="1.1"><circle cx="13" cy="9" r="7"/><path d="M6 9h14M13 2c3 3 3 11 0 14M13 2c-3 3-3 11 0 14"/><circle cx="5" cy="18" r="2"/><circle cx="21" cy="18" r="2"/><path d="M1 25c0-3 2-4 4-4s4 1 4 4M17 25c0-3 2-4 4-4s4 1 4 4"/></svg><h5 style="margin-bottom:4px">Social Impact Investing</h5>Focused on:<ul><li>Eliminating Poverty</li><li>Indigenous Reconciliation</li><li>Environmental Sustainability</li></ul></div>
  <div class="prog" style="left:10px;top:201px;height:97px;background:var(--blue-soft);color:var(--navy)"><svg viewBox="0 0 26 26" fill="none" stroke="#0b2f5b" stroke-width="1.1"><circle cx="6" cy="10" r="3"/><circle cx="13" cy="8" r="3"/><circle cx="20" cy="10" r="3"/><path d="M1 19c0-4 2-6 5-6s5 2 5 6M8 17c0-4 2-6 5-6s5 2 5 6M15 19c0-4 2-6 5-6s5 2 5 6"/></svg><h5>Revenue Development</h5>Supporting organizations with strategic planning, fundraising, and donor engagement.</div>
  <div class="prog" style="left:140px;top:201px;height:97px;background:var(--blue-soft);color:var(--navy)"><svg viewBox="0 0 26 26" fill="none" stroke="#0b2f5b" stroke-width="1.1"><path d="M16 8c0-4 3-6 6-6 0 4-3 6-6 6zM16 8c0-3-2-5-5-5 0 3 2 5 5 5zM16 8v4"/><rect x="1" y="14" width="11" height="3" rx="1"/><rect x="1" y="18" width="11" height="3" rx="1"/><rect x="1" y="22" width="11" height="3" rx="1"/><circle cx="18" cy="19" r="5"/><path d="M19 17c-1-.5-2.5-.3-2.5.7s2.5.8 2.5 2-1.7 1.2-2.5.6M18 16v6"/></svg><h5>Alternative Revenue Opportunities</h5>Including community bonds and innovative funding solutions for long-term impact.</div>
  <p class="abs body" style="left:26px;top:314px;width:220px;color:var(--navy)">Together, these programs strengthen communities and empower meaningful change.</p>
  <footer class="footer"><span class="brand"><span class="dot"></span>Velomar</span><span>2025 Annual Report</span></footer>
</section>

<!-- Back Cover -->
<section class="page" style="left:916px;top:484px;background:var(--navy)">
  <svg class="abs" style="left:0;top:0" width="271" height="384" viewBox="0 0 271 384" role="img" aria-label="Photograph of a lighthouse on a rocky coastal cliff at sunset with a path through wildflowers">
    <defs><linearGradient id="coast" x1="0" y1="0" x2="0" y2="1"><stop offset="0" stop-color="#2a4e7e"/><stop offset=".35" stop-color="#8a7a62"/><stop offset=".5" stop-color="#f0a64a"/><stop offset=".7" stop-color="#6a4a28"/><stop offset="1" stop-color="#2a2a1a"/></linearGradient></defs>
    <path d="M271 0H190C150 50 135 150 140 240C144 310 160 360 175 384H271Z" fill="url(#coast)"/>
  </svg>
  <p class="abs" style="left:20px;top:38px;width:150px;font-family:'Playfair Display',Georgia,serif;font-weight:700;font-size:15.5px;line-height:1.6;color:var(--white)">Together, we turn generosity into <span class="green">lasting impact.</span></p>
  <div class="abs" style="left:20px;top:132px;width:34px;height:2px;background:var(--green)"></div>
  <p class="abs" style="left:20px;top:159px;font-size:8.4px;font-weight:700;color:var(--green)">Let’s Build What’s Next.</p>
  <div class="contact" style="top:199px"><svg viewBox="0 0 14 14" fill="none" stroke="#7ab03a" stroke-width="1.1"><path d="M3 1l2.5 3-1.5 1.5c.8 2 2.5 3.7 4.5 4.5L10 8.5l3 2.5-1.5 2C6 13 1 8 1 2.5z"/></svg>555-014-2298</div>
  <div class="contact" style="top:223px"><svg viewBox="0 0 14 14" fill="none" stroke="#7ab03a" stroke-width="1.1"><rect x="1" y="3" width="12" height="9" rx="1"/><path d="M1 4l6 4 6-4"/></svg>info@velomar.ca</div>
  <div class="contact" style="top:247px"><svg viewBox="0 0 14 14" fill="none" stroke="#7ab03a" stroke-width="1.1"><circle cx="7" cy="7" r="6"/><ellipse cx="7" cy="7" rx="2.5" ry="6"/><path d="M1 7h12M2 4h10M2 10h10"/></svg>www.velomar.ca</div>
  <div class="abs brand" style="left:22px;top:300px;font-size:21px;gap:6px"><span class="dot" style="width:17px;height:17px;border-width:2px"></span>Velomar</div>
  <p class="abs" style="left:21px;top:332px;font-size:10.5px;font-weight:800;color:var(--white)">Values Driving <span class="green">Value</span></p>
</section>

</body>
</html>
```